Theatrical Producer/Consultant needs Artistic Brochure Shell and Inserts

Lanternfield Stageworks (www.lanternfieldstageworks.com) is a small company that offers theatrical producing and consulting services. We would like to create a brochure that contains information about our various productions and services. Because our roster is fluid, we are proposing to create a brochure shell or folder with pockets, and then a template for individual tear sheets that would be inserted into the inside pockets of the brochure shell/folder. The shell is intended for reuse each season, and new tear sheets will be developed separately on a project by project basis.
This task is to create the shell and a corresponding tear sheet template.
The brochure will be delivered by hand as well as by mail, so should fit into a standard size mailing envelope (i.e., within NPDS flat dimensions of 6 1/8" x 11 1/2")
The final design should reflect the high level of artistry of our theatrical projects. Attached are our logo as well as photos of current theatrical offerings which are available for use on the brochure shell but not required. There is also a file that describes our services in more detail, fyi. This will ultimately go onto one of the tear sheets in the brochure.
For the tear sheet template, we have also included a sample brochure from a peer colleague, just to give you an idea of the kind of information each sheet would contain. Each project page will contain title of the project, information about the artists involved, one or more photos, a project description, schedule, fee and other technical information.
The final files for both the shell and tear sheet templates should be printer-ready and also in a file format that we can edit ourselves in future.
Updates
Project Deadline Extended Reason: There was a discrepancy between posted project deadline (December 7) and when project was automatically closed (December 6). Since several designers who have not yet submitted indicated they were planning to submit designs, we wanted to make sure that they were able to do so. Added Monday, December 7, 2015
Industry/Entity Type
Performing Art
Font styles to use
Look and feel
Each slider illustrates characteristics of the customer's brand and the style your logo design should communicate.

```html
<!DOCTYPE html>
<html lang="en">
<head>
<meta charset="utf-8">
<title>Lanternfield Stageworks – Insert Templates</title>
<link href="https://fonts.googleapis.com/css2?family=Lato:wght@300;400;700&family=Montserrat:wght@400&display=swap" rel="stylesheet">
<style>
:root{
  --board:#323232;
  --ink:#3a3a3a;
  --ink-soft:#666;
  --rule:#4a4a4a;
  --teal:#169db6;
  --teal-deep:#0f8ea6;
  --sky:#a7d6e1;
  --sky-light:#e3f2f6;
  --band:#a3d3de;
  --white:#fff;
}
*{margin:0;padding:0;box-sizing:border-box}
html,body{width:786px;height:1200px;overflow:hidden}
body{background:var(--board);font-family:"Lato",sans-serif;color:var(--ink);position:relative}
.board-label{position:absolute;color:var(--white);font-family:"Montserrat",sans-serif;font-size:13px;text-align:center;width:332px}
.panel{position:absolute;overflow:hidden}
.photo{position:absolute;border-radius:50%;border:2px solid var(--white);
  background:radial-gradient(circle at 55% 70%,#c8242a 0 12%,transparent 13%),
  linear-gradient(180deg,#4a2a18 0%,#b88a4a 30%,#7a4a28 48%,#b0232a 62%,#8a1c20 100%);
  box-shadow:0 0 0 1px rgba(0,0,0,.08)}
.act-title{position:absolute;font-weight:300;font-size:29px;line-height:1;color:#222;text-align:right}
.act-sub{position:absolute;font-size:7.5px;color:#222;text-align:right}
.credits{position:absolute}
.credit dt{font-size:5.5px;font-weight:700;color:#222;margin-top:6px}
.credit dd{font-size:8px;color:var(--ink-soft);padding:2px 0 3px;border-bottom:1px solid var(--rule)}
.credit dd+dd{margin-top:1px}
.credit.cast dd{border:none;padding:1px 0}
.credit.cast dd:last-child{border-bottom:1px solid var(--rule);padding-bottom:4px}
.tear-sheet .credit dd{color:#333}
.checks{position:absolute;list-style:none;font-size:8px;color:var(--ink-soft)}
.checks li{display:flex;align-items:center;gap:4px;margin-bottom:7px}
.checks svg{width:7px;height:7px}
.lorem{font-size:6.6px;line-height:1.65;color:#777;text-align:justify}
.dates-title{position:absolute;font-size:11px;font-weight:300;color:#555}
.dates{position:absolute;list-style:none;border-left:1px solid #555;padding-left:7px;font-size:6.8px;font-weight:300;color:#555;line-height:12.9px}
.folio{position:absolute;font-size:5.4px;color:#555}

/* Template 1 */
.cover{left:40px;top:70px;width:332px;height:500px;
  background:linear-gradient(180deg,#fff 0%,#fff 22%,#d8eef3 38%,#7ccbd9 62%,var(--teal) 82%,var(--teal-deep) 100%)}
.cover-heading{position:absolute;left:113px;top:22px;font-weight:300;font-size:36px;line-height:.98;color:#333}
.cover-glow{position:absolute;left:20px;top:110px;width:300px;height:300px;border-radius:50%;
  background:radial-gradient(circle,rgba(255,255,255,.0) 40%,rgba(120,200,215,.35) 60%,rgba(255,255,255,0) 72%)}
.cover .photo{left:53px;top:132px;width:190px;height:190px;border-width:3px}
.cover-kicker{position:absolute;left:43px;top:379px;font-size:15.5px;color:var(--white)}
.cover-text{position:absolute;left:42px;top:405px;width:278px;font-size:9.5px;line-height:12.4px;color:#eaf7fa;font-weight:300}

/* Template 2 */
.t2{left:414px;top:70px;width:328px;height:494px;
  background:linear-gradient(180deg,#fff 0%,#fff 30%,var(--sky-light) 50%,var(--sky) 100%)}
.t2 .act-title{right:14px;top:14px}
.t2 .title-rule{position:absolute;left:0;right:14px;top:44px;border-top:1px solid #222}
.t2 .act-sub{right:14px;top:48px}
.t2 .photo{left:22px;top:60px;width:136px;height:136px}
.t2 .credits{left:171px;top:62px;width:143px}
.t2 .checks{left:19px;top:221px}
.t2 .band{position:absolute;left:0;right:0;top:260px;height:66px;background:var(--band);padding:7px 14px 0 19px}
.t2 .dates-title{left:21px;top:338px}
.t2 .dates{left:21px;top:356px}
.t2 .folio{right:10px;top:479px}

/* Template 3 */
.t3{left:40px;top:640px;width:334px;height:502px;
  background:linear-gradient(180deg,#fff 0%,#f4fafc 30%,var(--sky) 100%)}
.t3 .sidebar{position:absolute;left:0;top:0;width:170px;height:100%;
  background:linear-gradient(180deg,var(--sky) 0%,#d2ebf1 40%,var(--sky-light) 60%,var(--sky) 100%)}
.t3 .photo{left:18px;top:10px;width:142px;height:142px}
.t3 .credits{left:14px;top:154px;width:146px}
.t3 .checks{left:14px;top:371px}
.t3 .act-title{right:14px;top:16px}
.t3 .act-sub{right:18px;top:47px}
.t3 .copy{position:absolute;left:179px;top:75px;width:141px}
.t3 .copy p+p{margin-top:6px}
.t3 .dates-title{left:179px;top:318px}
.t3 .dates{left:179px;top:336px}
.t3 .folio{left:11px;top:484px}

/* Template 4 */
.t4{left:410px;top:640px;width:332px;height:502px;
  background:linear-gradient(180deg,#fff 0%,#fff 15%,#eef7f9 40%,var(--sky) 100%)}
.t4 .act-title{right:14px;top:16px}
.t4 .title-rule{position:absolute;left:104px;right:14px;top:44px;border-top:1px solid #222}
.t4 .act-sub{right:14px;top:48px}
.t4 .credits{left:13px;top:66px;width:157px}
.t4 .copy{position:absolute;left:178px;top:74px;width:140px}
.t4 .dates-title{left:178px;top:198px}
.t4 .dates{left:178px;top:216px}
.t4 .folio{left:11px;top:484px}
</style>
</head>
<body>

<div class="board-label" style="left:40px;top:38px">Insert Template 1</div>
<div class="board-label" style="left:412px;top:38px">Insert Template 2</div>
<div class="board-label" style="left:40px;top:609px">Insert Template 3</div>
<div class="board-label" style="left:410px;top:609px">Insert Template 4</div>

<!-- Template 1: cover -->
<section class="panel cover">
  <h1 class="cover-heading">new<br>productions</h1>
  <div class="cover-glow"></div>
  <div class="photo" role="img" aria-label="Photo of a performer in a red dress on stage in an ornate red-seated theatre"></div>
  <h2 class="cover-kicker">Claritas est etiam processus dynamicus</h2>
  <p class="cover-text">Lorem ipsum dolor sit amet, consectetuer adipiscing elit, sed diam nonummy nibh euismod tincidunt ut laoreet dolore magna aliquam erat volutpat. Ut wisi enim ad minim veniam, quis nostrud exerci tation ullamcorper suscipit lobortis nisl ut aliquip ex ea commodo consequat.</p>
</section>

<!-- Template 2 -->
<section class="panel t2 tear-sheet">
  <h1 class="act-title">Act Name</h1>
  <div class="title-rule"></div>
  <p class="act-sub">Based on the Act Name</p>
  <div class="photo" role="img" aria-label="Photo of a performer in a red dress on stage in an ornate red-seated theatre"></div>
  <dl class="credits">
    <div class="credit"><dt>Text By</dt><dd>Martin Hale, Jean-Luc Marchand</dd><dd>and Marie-Claire Devaux</dd></div>
    <div class="credit"><dt>Directed by</dt><dd>Martin Hale &amp; Marie-Claire Devaux</dd></div>
    <div class="credit"><dt>Music</dt><dd>Kenji Morisaki</dd></div>
    <div class="credit"><dt>Lighting</dt><dd>Philippe Roussel</dd></div>
    <div class="credit cast"><dt>With</dt><dd>Claire Mbeki,</dd><dd>Jordan Ellis, Eric Nduwayo</dd><dd>and Sean O'Malley</dd></div>
  </dl>
  <ul class="checks">
    <li><svg viewBox="0 0 8 8"><rect x=".5" y=".5" width="7" height="7" fill="none" stroke="#555"/><path d="M1.8 4l1.5 1.6L6.3 2" fill="none" stroke="#555" stroke-width="1.1"/></svg>Show performedin English</li>
    <li><svg viewBox="0 0 8 8"><rect x=".5" y=".5" width="7" height="7" fill="none" stroke="#555"/><path d="M1.8 4l1.5 1.6L6.3 2" fill="none" stroke="#555" stroke-width="1.1"/></svg>Duration : 1h30 (tbc)</li>
  </ul>
  <div class="band"><p class="lorem">Lorem ipsum dolor sit amet, consectetuer adipiscing elit, sed diam nonummy nibh euismod tincidunt ut laoreet dolore magna aliquam erat volutpat. Ut wisi enim ad minim veniam, quis nostrud exerci tation ullamcorper suscipit lobortis nisl ut aliquip ex ea commodo consequat. Duis autem vel eum iriure dolor in hendrerit in vulputate velit esse molestie consequat.</p></div>
  <h2 class="dates-title">Performance Dates</h2>
  <ul class="dates">
    <li>Sept. 15 to Oct. 17, 2015 Théâtre des Lanternes</li>
    <li>Nov. 17 to 21, 2015 Harbour Repertory Theatre/Singapore</li>
    <li>Nov. 25 to 29 , 2015 Kiri Theatre/Tokyo/Japan*</li>
    <li>Dec . 10 to 11, 2015 Maison des Arts de Lune</li>
    <li>Feb . 3 to 27, 2016 Eastbank Theatre/London/Great Britain</li>
    <li>March 5 to 12 , 2016 Mumbai/India*</li>
    <li>March 16 to 20, 2016 Bayview Arts Festival</li>
    <li>May 11 to 15 , 2016 Teatro Solare/Rome/Italia</li>
  </ul>
  <p class="folio">NEW PRODUCTION 2015/2016</p>
</section>

<!-- Template 3 -->
<section class="panel t3 tear-sheet">
  <aside class="sidebar">
    <div class="photo" role="img" aria-label="Photo of a performer in a red dress on stage in an ornate red-seated theatre"></div>
    <dl class="credits">
      <div class="credit"><dt>Text By</dt><dd>Martin Hale, Jean-Luc Marchand</dd><dd>and Marie-Claire Devaux</dd></div>
      <div class="credit"><dt>Directed by</dt><dd>Martin Hale &amp; Marie-Claire Devaux</dd></div>
      <div class="credit"><dt>Music</dt><dd>Kenji Morisaki</dd></div>
      <div class="credit"><dt>Lighting</dt><dd>Philippe Roussel</dd></div>
      <div class="credit cast"><dt>With</dt><dd>Claire Mbeki,</dd><dd>Jordan Ellis, Eric Nduwayo</dd><dd>and Sean O'Malley</dd></div>
    </dl>
    <ul class="checks">
      <li style="padding-left:11px">Show performedin English</li>
      <li><svg viewBox="0 0 8 8"><rect x=".5" y=".5" width="7" height="7" fill="none" stroke="#555"/><path d="M1.8 4l1.5 1.6L6.3 2" fill="none" stroke="#555" stroke-width="1.1"/></svg>Duration : 1h30 (tbc)</li>
    </ul>
    <p class="folio">NEW PRODUCTION 2015/2016</p>
  </aside>
  <h1 class="act-title">Act Name</h1>
  <p class="act-sub">Based on the Act Name</p>
  <div class="copy">
    <p class="lorem">Lorem ipsum dolor sit amet, consectetuer adipiscing elit, sed diam nonummy nibh euismod tincidunt ut laoreet dolore magna aliquam erat volutpat. Ut wisi enim ad minim veniam, quis nostrud exerci tation ullamcorper suscipit lobortis nisl ut aliquip ex ea commodo consequat. Duis autem vel eum iriure dolor in hendrerit in vulputate velit esse molestie consequat.</p>
    <p class="lorem">Lorem ipsum dolor sit amet, consectetuer adipiscing elit, sed diam nonummy nibh euismod tincidunt ut laoreet dolore magna aliquam erat volutpat. Ut wisi enim ad minim veniam, quis nostrud exerci tation ullamcorper suscipit lobortis nisl ut aliquip ex ea commodo consequat. Duis autem vel eum iriure dolor in hendrerit in vulputate velit esse molestie consequat.</p>
  </div>
  <h2 class="dates-title">Performance Dates</h2>
  <ul class="dates">
    <li>Sept. 15 to Oct. 17, 2015</li>
    <li>Théâtre des Lanternes</li>
    <li>Nov. 17 to 21, 2015</li>
    <li>Harbour Repertory Theatre/Singapore</li>
    <li>Nov. 25 to 29 , 2015</li>
    <li>Kiri Theatre/Tokyo/Japan*</li>
    <li>Dec . 10 to 11, 2015</li>
    <li>Maison des Arts de Lune</li>
    <li>Feb . 3 to 27, 2016</li>
    <li>Eastbank Theatre/London/Great Britain</li>
  </ul>
</section>

<!-- Template 4 -->
<section class="panel t4 tear-sheet">
  <h1 class="act-title">Act Name</h1>
  <div class="title-rule"></div>
  <p class="act-sub">Based on the Act Name</p>
  <dl class="credits">
    <div class="credit"><dt>Text By</dt><dd>Martin Hale, Jean-Luc Marchand</dd><dd>and Marie-Claire Devaux</dd></div>
    <div class="credit"><dt>Directed by</dt><dd>Martin Hale &amp; Marie-Claire Devaux</dd></div>
    <div class="credit"><dt>Music</dt><dd>Kenji Morisaki</dd></div>
    <div class="credit"><dt>Lighting</dt><dd>Philippe Roussel</dd></div>
    <div class="credit cast"><dt>With</dt><dd>Claire Mbeki,</dd><dd>Jordan Ellis, Eric Nduwayo</dd><dd>and Sean O'Malley</dd></div>
  </dl>
  <div class="copy">
    <p class="lorem">Lorem ipsum dolor sit amet, consectetuer adipiscing elit, sed diam nonummy nibh euismod tincidunt ut laoreet dolore magna aliquam erat volutpat. Ut wisi enim ad minim veniam, quis nostrud exerci tation ullamcorper suscipit lobortis nisl ut aliquip ex ea commodo consequat. Duis autem vel eum iriure dolor in hendrerit in vulputate velit esse molestie consequat.</p>
  </div>
  <h2 class="dates-title">Performance Dates</h2>
  <ul class="dates">
    <li>Sept. 15 to Oct. 17, 2015</li>
    <li>Théâtre des Lanternes</li>
    <li>Nov. 17 to 21, 2015</li>
    <li>Harbour Repertory Theatre/Singapore</li>
  </ul>
  <p class="folio">NEW PRODUCTION 2015/2016</p>
</section>

</body>
</html>
```